Vortaleen - Lead the Way!

Vortaleen is a new Silicon Valley company, of the pimrela founders from Berlin, which provides a "Shared Hive Circle". This platform allows the crowd to support startups with money, experts and fame. Our Vision is, that everyone should become an entrepreneur.

Pls find all brief details in the attached document
Updates

Would be nice to have a list of more social services I'm available on, like a list of pictograms of all my services:

Find me on: chattro, fennwix+, qrt, mivrel, datebloom, pohk, rplex, etc...

pls make sure to use the right font:
http://www.typelarder-demo.com/fonts/Orbitron

Target Market(s)

Main target market is those already involved in the startup industry, by fundraising, investing, advising, cofounding and working. Vortaleen brings a totaly new transparency and collaborative way of starting companies to that business.

· Entrepreneurs (looking for funding, team and community)
· Investors (looking for hot investments and )
· Experts (workers looking for startups they can work for equity)
· Incubators & Business Schools (looking for tools to advise startups)

Industry/Entity Type

It Company

Requirements
Must have
• Pls find all brief details in the attached document
Nice to have

```html
<!DOCTYPE html>
<html lang="en">
<head>
<meta charset="utf-8">
<title>Vortaleen – Business Card</title>
<link rel="stylesheet" href="https://fonts.googleapis.com/css2?family=Exo:wght@400;500;600&display=swap">
<style>
  :root {
    --backdrop: #3a3532;
    --card-white: #ffffff;
    --brand-orange: #e4603c;
    --ink-grey: #5a5a5a;
    --label-grey: #8a8583;
    --social-blue: #4a7fb5;
  }
  * { box-sizing: border-box; margin: 0; padding: 0; }
  html, body {
    width: 840px; height: 1200px; overflow: hidden;
    background: var(--backdrop);
    font-family: "Exo", sans-serif;
  }
  .sheet { position: relative; width: 840px; height: 1200px; }

  .card {
    position: absolute; left: 100px; width: 642px; height: 371px;
    border-radius: 30px;
  }
  .card--front { top: 197px; background: var(--card-white); }
  .card--back { top: 651px; background: var(--brand-orange); color: var(--card-white); text-align: center; }

  .side-label {
    position: absolute; left: 0; width: 840px; text-align: center;
    font-size: 14px; color: var(--label-grey); letter-spacing: 0.5px;
  }
  .side-label--front { top: 591px; }
  .side-label--back { top: 1067px; }

  /* Front */
  .brand {
    position: absolute; left: 72px; top: 208px; text-align: left;
  }
  .brand__name {
    font-size: 29px; font-weight: 500; color: var(--brand-orange); line-height: 1;
  }
  .brand__tagline {
    margin-top: 4px; margin-left: 22px;
    font-size: 13px; color: var(--ink-grey);
  }
  .person { position: absolute; right: 60px; top: 100px; text-align: right; }
  .person__name {
    font-size: 29px; font-weight: 600; color: var(--brand-orange); letter-spacing: 1px; line-height: 1;
  }
  .person__role {
    margin-top: 8px; font-size: 19px; color: var(--ink-grey); letter-spacing: 0.5px;
  }
  .contact {
    position: absolute; right: 62px; top: 228px; text-align: right;
    font-size: 12.5px; line-height: 15px; color: var(--ink-grey);
  }
  .contact__label { color: var(--brand-orange); }
  .social {
    position: absolute; right: 62px; top: 279px; list-style: none;
    font-size: 9px; line-height: 10px; color: var(--ink-grey); text-align: right;
  }
  .social li { display: flex; justify-content: flex-end; align-items: center; gap: 5px; }
  .social__mark {
    display: inline-block; width: 7px; height: 7px; background: var(--social-blue);
  }

  /* Back */
  .pitch__title {
    margin-top: 78px; font-size: 29px; font-weight: 500; letter-spacing: 0.5px;
  }
  .pitch__list {
    list-style: none; margin-top: 18px; font-size: 13px; line-height: 17px;
  }
  .pitch__cta { margin-top: 6px; font-size: 16px; font-weight: 500; }
  .back__rule {
    position: absolute; left: 106px; top: 298px; width: 432px; height: 3px;
    background: var(--card-white); border-radius: 2px;
  }
  .addresses {
    position: absolute; left: 0; top: 314px; width: 642px;
    font-size: 9.5px; letter-spacing: 0.2px;
  }
</style>
</head>
<body>
<main class="sheet">

  <section class="card card--front" aria-label="Card front">
    <div class="brand">
      <div class="brand__name">Vortaleen</div>
      <div class="brand__tagline">Lead the Way!</div>
    </div>

    <div class="person">
      <h1 class="person__name">JONAS WERDLER</h1>
      <p class="person__role">FOUNDER AND CEO</p>
    </div>

    <div class="contact">
      <div><span class="contact__label">WEBSITE</span> www.vortaleen.io</div>
      <div><span class="contact__label">EMAIL</span> jw@vortaleen.io</div>
      <div><span class="contact__label">PHONE</span> 040 555 218 603</div>
    </div>

    <ul class="social">
      <li>chirpnet.io/jonaswerdler <span class="social__mark"></span></li>
      <li>friendra.io/jonaswerdler <span class="social__mark"></span></li>
      <li>linkory.io/in/jonaswerdler <span class="social__mark"></span></li>
    </ul>
  </section>
  <div class="side-label side-label--front">FRONT</div>

  <section class="card card--back" aria-label="Card back">
    <h2 class="pitch__title">Are you interested in?</h2>
    <ul class="pitch__list">
      <li>• Starting your own Business?</li>
      <li>• Investing in hot Startups?</li>
      <li>• Working for the next “Friendra”?</li>
    </ul>
    <p class="pitch__cta">Join us on Friendra.io/Vortaleen</p>
    <div class="back__rule"></div>
    <p class="addresses">Berlin - Lindenhofstraße 42 . 10969 Berlin . Germany &nbsp;•&nbsp; Silicon Valley - 218 Orchard Loop . Sunnyvale . CA 94089</p>
  </section>
  <div class="side-label side-label--back">BACK</div>

</main>
</body>
</html>
```